PPE EQIUPMENT

WE WOULD LIKE TO PRODUCE 2 DIFFERENT BANNERS TO BE PLACED OUTSIDE OF OUR WAREHOUSE TO ADVERTISE THAT WE HAVE FACE MASKS, HAND SANITISERS, DISINFECTANT SPRAY, FACE SHIELDS AND HAND SOAP. THE SIZE OF EACH BANNER WILL BE , portrait to be (W) 140 cm x (H) 250 cm, with 4 x eyelets. THE BANNER IS TO STATE PPE EQUIPMENT AVAILABLE HERE AND SHOW OUR PHONE NUMBER 0208-417-2953. FINALLY WE WILL REQUIRE SOME IMAGES OF THE PRODUCTS IF YOU CAN SUPPLY THESE. THANKS

```html
<!DOCTYPE html>
<html lang="en">
<head>
<meta charset="utf-8">
<title>PPE Equipment Banner</title>
<link rel="stylesheet" href="https://fonts.googleapis.com/css2?family=Anton&family=Archivo+Black&family=Arimo&family=Barlow:wght@300;500&family=Bebas+Neue&display=swap">
<style>
  :root {
    --navy: #1f3a6f;
    --white: #ffffff;
    --backdrop: #d6d6d6;
    --eyelet: #7a7a7a;
    --eyelet-dark: #12244a;
    --icon-fill: #dfe6f2;
  }
  * { margin: 0; padding: 0; box-sizing: border-box; }
  html, body { width: 960px; height: 1200px; overflow: hidden; }
  body { background: var(--backdrop); position: relative; }

  .banner {
    position: absolute; left: 162px; top: 30px;
    width: 636px; height: 1140px;
    background: var(--white);
  }
  .eyelet {
    position: absolute; width: 30px; height: 30px; border-radius: 50%;
    border: 5px solid var(--eyelet); background: transparent;
  }
  .eyelet.top-left { left: 14px; top: 13px; }
  .eyelet.top-right { right: 14px; top: 13px; }
  .eyelet.bottom { border-color: var(--eyelet-dark); top: 1097px; }
  .eyelet.bottom-left { left: 14px; }
  .eyelet.bottom-right { right: 14px; }

  .headline {
    position: absolute; left: 0; right: 0; top: 48px;
    text-align: center; color: var(--navy);
    font-family: "Anton", sans-serif; font-size: 96px; line-height: 1;
    letter-spacing: -1px;
  }
  .subline {
    position: absolute; left: 0; right: 0; top: 157px;
    text-align: center; color: var(--navy);
    font-family: "Arimo", sans-serif; font-size: 50px; line-height: 1;
  }
  .phone-band {
    position: absolute; left: 0; right: 0; top: 222px; height: 111px;
    background: var(--navy); color: var(--white);
    display: flex; align-items: center; justify-content: center;
    font-family: "Archivo Black", sans-serif; font-size: 66px; letter-spacing: 1px;
  }

  .product-list { position: absolute; left: 0; right: 0; top: 355px; list-style: none; }
  .product {
    position: absolute; left: 0; right: 0; height: 113px;
  }
  .product-icon {
    position: absolute; left: 36px; top: 0; width: 147px; height: 113px;
    border: 8px solid var(--navy); border-radius: 10px;
    background: var(--icon-fill);
  }
  .product-label {
    position: absolute; left: 198px; top: 10px; width: 408px; height: 90px;
    background: var(--navy); color: var(--white);
    display: flex; align-items: center; padding-left: 22px;
    font-family: "Bebas Neue", sans-serif; font-size: 60px; line-height: 1;
    letter-spacing: -0.5px; padding-top: 4px;
  }

  .brand-band {
    position: absolute; left: 0; right: 0; top: 973px; height: 167px;
    background: var(--navy); color: var(--white); text-align: center;
  }
  .brand-name {
    position: absolute; left: 0; right: 0; top: 28px;
    font-family: "Barlow", sans-serif; font-weight: 500; font-size: 54px;
    line-height: 1; letter-spacing: 1px;
  }
  .brand-tagline {
    position: absolute; left: 0; right: 0; top: 92px;
    font-family: "Barlow", sans-serif; font-weight: 300; font-size: 32px;
    line-height: 1; letter-spacing: 1px;
  }
</style>
</head>
<body>
  <main class="banner">
    <span class="eyelet top-left"></span>
    <span class="eyelet top-right"></span>

    <h1 class="headline">PPE EQUIPMENT</h1>
    <p class="subline">AVAILABLE HERE</p>

    <div class="phone-band">0208-417-2953</div>

    <ul class="product-list">
      <li class="product" style="top:0">
        <div class="product-icon" role="img" aria-label="Face mask icon"></div>
        <div class="product-label">FACE MASKS</div>
      </li>
      <li class="product" style="top:120px">
        <div class="product-icon" role="img" aria-label="Hands under a sanitiser pump bottle icon"></div>
        <div class="product-label">HAND SANITISERS</div>
      </li>
      <li class="product" style="top:240px">
        <div class="product-icon" role="img" aria-label="Disinfectant spray bottle icon"></div>
        <div class="product-label">DISINFECTANT SPRAY</div>
      </li>
      <li class="product" style="top:360px">
        <div class="product-icon" role="img" aria-label="Face shield icon"></div>
        <div class="product-label">FACE SHIELDS</div>
      </li>
      <li class="product" style="top:480px">
        <div class="product-icon" role="img" aria-label="Hand holding a bar of soap icon"></div>
        <div class="product-label">HAND SOAP</div>
      </li>
    </ul>

    <footer class="brand-band">
      <p class="brand-name">NORTHGATE SUPPLIES</p>
      <p class="brand-tagline">WHOLESALE TRADE STOCKISTS</p>
    </footer>

    <span class="eyelet bottom bottom-left"></span>
    <span class="eyelet bottom bottom-right"></span>
  </main>
</body>
</html>
```